Join Wait / Reservations Handout

This is a handout for guests with information about the ability to join our
waitlist and/or make reservations. It will be handed out to any guest that ends up waiting on our waitlist to be seated. It will describe how our waitlist and reservations system works. It is informational for them to download our mobile app.

It was forcing me to move the look and feel sliders. Please refer to our branding guide for look and feel.

Industry/Entity Type

Hospitality

Contact Information for Business Card

One of the attached documents give a very generic layout of the information we need on this card. This layout is more for where we wanted the information placed and has nothing to do with the design aspects of the piece. Please use your imagination. Any of the 5 colors in the branding guide can be used anywhere. The pineapple design can be used anywhere in any color combination.

If you require any other files please let me know. Thanks

Other font styles liked:
• Please see attached branding guide

Requirements
Must have
• The only color requirement is that the logo be the blue with teal lettering...This has to match our app store logo.

```html
<!DOCTYPE html>
<html lang="en">
<head>
<meta charset="utf-8">
<title>Save the Wait – Guest Handout</title>
<link rel="stylesheet" href="https://fonts.googleapis.com/css2?family=Jost:wght@300;400;500;700;800&display=swap">
<style>
  :root {
    --navy: #0f2a45;
    --teal: #4d9c9e;
    --teal-light: #6fb3b3;
    --paper: #ffffff;
    --pattern: #eceeef;
    --stage: #e6e6e8;
  }
  * { box-sizing: border-box; margin: 0; padding: 0; }
  html, body { width: 1200px; height: 863px; overflow: hidden; }
  body {
    background: var(--stage);
    font-family: "Jost", "Futura", sans-serif;
    color: var(--navy);
    position: relative;
  }
  .card {
    position: absolute;
    top: 143px;
    width: 330px;
    height: 577px;
    background: var(--paper);
    box-shadow: 0 6px 20px rgba(0,0,0,0.12);
    overflow: hidden;
  }
  .card--info { left: 230px; }
  .card--promo { left: 640px; }

  /* Info side */
  .info-block { position: absolute; left: 0; right: 0; }
  .info-block--right { text-align: right; padding-right: 28px; }
  .info-title {
    font-weight: 800;
    font-size: 17px;
    letter-spacing: 0.2px;
    text-transform: uppercase;
    line-height: 1.2;
  }
  .info-text {
    font-weight: 300;
    font-size: 15px;
    line-height: 1.25;
    color: var(--teal);
  }
  .join { top: 44px; }
  .reserve {
    top: 118px; left: 24px; right: 30px;
    background: var(--teal);
    padding: 14px 16px;
  }
  .reserve .info-text { color: #fff; }
  .buffet { top: 262px; }
  .groups {
    top: 372px; left: 24px; right: 30px;
    background: var(--navy);
    color: #fff;
    padding: 14px 16px;
  }
  .groups .info-title { color: #fff; }
  .groups .info-text { color: var(--teal-light); }

  /* Promo side */
  .promo-pattern { position: absolute; inset: 0; background: var(--pattern); }
  .headline {
    position: absolute; top: 52px; left: 30px;
    font-weight: 800; font-size: 44px; line-height: 0.98;
    text-transform: uppercase; letter-spacing: 0.5px;
  }
  .app-pill {
    position: absolute; top: 156px; left: 30px; right: 28px;
    height: 32px; border-radius: 16px;
    background: var(--teal); color: #fff;
    font-size: 15px; font-weight: 400; letter-spacing: 3px;
    text-transform: uppercase; text-align: center; line-height: 32px;
  }
  .brand {
    position: absolute; top: 222px; left: 0; right: 0;
    display: flex; flex-direction: column; align-items: center; gap: 12px;
  }
  .brand-square { width: 64px; height: 64px; background: var(--navy); }
  .brand-name {
    font-weight: 700; font-size: 24px; letter-spacing: 2px;
    text-transform: uppercase; color: var(--navy);
  }
  .search { position: absolute; top: 380px; left: 0; right: 0; text-align: center; }
  .search-label {
    font-weight: 500; font-size: 19px; letter-spacing: 6px;
    color: var(--teal); text-transform: uppercase;
  }
  .search-term { font-weight: 400; font-size: 16px; }
  .stores {
    position: absolute; top: 458px; left: 0; right: 0;
    display: flex; justify-content: center; gap: 14px;
  }
  .store-dot { width: 30px; height: 30px; border-radius: 50%; background: var(--navy); }
  .footer-band {
    position: absolute; left: 0; right: 0; bottom: 0; height: 40px;
    background: var(--navy);
  }
</style>
</head>
<body>
  <section class="card card--info" aria-label="Waitlist and reservation details">
    <div class="info-block info-block--right join">
      <h2 class="info-title">When to join the wait</h2>
      <p class="info-text">Anytime</p>
    </div>
    <div class="info-block reserve">
      <h2 class="info-title">When to reserve</h2>
      <p class="info-text">Anytime – 2 hours in advance<br>(excluding weekend, open - 2pm)</p>
    </div>
    <div class="info-block info-block--right buffet">
      <h2 class="info-title">Sunday buffet</h2>
      <p class="info-text">Sunday + Holiday Buffets<br>(Coming June 2018)</p>
    </div>
    <div class="info-block groups">
      <h2 class="info-title">Large groups</h2>
      <p class="info-text">Large Groups handled/contacted<br>by Catering manager</p>
    </div>
  </section>

  <section class="card card--promo" aria-label="App download">
    <div class="promo-pattern" role="img" aria-label="Faint geometric background pattern"></div>
    <h1 class="headline">Save<br>the wait...</h1>
    <div class="app-pill">Download our app</div>
    <div class="brand">
      <div class="brand-square" aria-hidden="true"></div>
      <span class="brand-name">Harborline</span>
    </div>
    <div class="search">
      <p class="search-label">Search</p>
      <p class="search-term">“Harborline East Mill”</p>
    </div>
    <div class="stores" aria-label="Available in app stores">
      <span class="store-dot" aria-hidden="true"></span>
      <span class="store-dot" aria-hidden="true"></span>
    </div>
    <div class="footer-band"></div>
  </section>
</body>
</html>
```